its a new company based in Christchurch new Zealand building computers ,repairs, upgrades and anything computers for the general public,i like bright happy colours like yellows, greens reds anything that stands out and it needs to communicant trust and security towards my new company,i have no logo yet,

Target Market(s)

target market of all ages

Industry/Entity Type

Building

Contact Information for Business Card

Byte Harbour Limited,ph-0218847261,email-tidelark77@mailvesta.test,14c marlowe cres,fenwick

```html
<!DOCTYPE html>
<html lang="en">
<head>
<meta charset="utf-8">
<title>Byte Harbour Limited – Business Cards</title>
<link rel="stylesheet" href="https://fonts.googleapis.com/css2?family=Exo+2:wght@400;500;600&family=Oswald:wght@500&display=swap">
<style>
  :root {
    --bg: #e9e6e1;
    --card: #ffffff;
    --blue: #0aa3d3;
    --purple: #865588;
    --band: #c8e8f4;
    --ink: #2a2a2a;
    --edge: #1e1e1e;
    --muted: #555555;
  }
  * { box-sizing: border-box; margin: 0; padding: 0; }
  html, body { width: 1200px; height: 970px; overflow: hidden; }
  body {
    background: var(--bg);
    font-family: "Exo 2", sans-serif;
    color: var(--ink);
    position: relative;
  }
  .card {
    position: absolute;
    left: 250px;
    width: 700px;
    height: 400px;
    background: var(--card);
    box-shadow: 0 6px 18px rgba(0,0,0,.18);
    overflow: hidden;
  }
  .card--back { top: 55px; }
  .card--front { top: 515px; }
  .card__shapes { position: absolute; inset: 0; }

  .brand {
    position: absolute;
    display: flex;
    align-items: center;
    gap: 10px;
    font-family: "Exo 2", sans-serif;
    font-weight: 500;
    color: var(--blue);
    white-space: nowrap;
  }
  .brand__dot {
    width: 14px; height: 14px;
    border-radius: 50%;
    background: var(--purple);
    flex: none;
  }
  .card--back .brand { left: 40px; top: 190px; font-size: 30px; }
  .card--front .brand { left: 40px; top: 96px; font-size: 24px; }

  .website-strip {
    position: absolute;
    left: 120px; top: 346px;
    font-size: 15px;
    letter-spacing: 4px;
    color: #ffffff;
  }

  .title-band {
    position: absolute;
    left: 40px; top: 170px;
    height: 45px;
    display: flex;
    align-items: center;
    gap: 12px;
  }
  .title-band__name {
    font-family: "Oswald", sans-serif;
    font-weight: 500;
    font-size: 24px;
    letter-spacing: 1px;
    color: var(--ink);
  }
  .title-band__divider { width: 2px; height: 26px; background: var(--ink); }
  .title-band__role {
    font-size: 14px;
    letter-spacing: 2px;
    color: var(--muted);
  }

  .contacts {
    position: absolute;
    left: 40px; top: 240px;
    padding-left: 16px;
    border-left: 1.5px solid var(--ink);
    display: grid;
    grid-template-columns: 180px 230px;
    row-gap: 16px;
    column-gap: 20px;
    font-size: 14px;
    color: var(--ink);
  }
  .contact { display: flex; align-items: center; gap: 8px; white-space: nowrap; }
  .contact--wide { grid-column: 1 / span 2; }
  .contact__icon { width: 22px; height: 22px; flex: none; }
</style>
</head>
<body>

  <section class="card card--back" aria-label="Card back">
    <svg class="card__shapes" viewBox="0 0 700 400" aria-hidden="true">
      <polygon points="330,0 700,0 700,130 390,250" fill="var(--blue)"/>
      <polygon points="0,300 390,250 700,130 700,400 0,400" fill="var(--purple)"/>
      <polyline points="330,0 390,250 700,130" fill="none" stroke="var(--edge)" stroke-width="4"/>
    </svg>
    <div class="brand"><span class="brand__dot"></span>Byte Harbour Limited</div>
    <p class="website-strip">www.byteharbour.test</p>
  </section>

  <section class="card card--front" aria-label="Card front">
    <svg class="card__shapes" viewBox="0 0 700 400" aria-hidden="true">
      <polygon points="0,170 465,170 493,215 0,215" fill="var(--band)"/>
      <polygon points="120,0 560,0 440,130" fill="var(--blue)"/>
      <polygon points="560,0 700,0 700,400 610,400 440,130" fill="var(--purple)"/>
      <polyline points="120,0 440,130 560,0" fill="none" stroke="var(--edge)" stroke-width="4"/>
      <line x1="440" y1="130" x2="610" y2="400" stroke="var(--edge)" stroke-width="4"/>
    </svg>

    <div class="brand"><span class="brand__dot"></span>Byte Harbour Limited</div>

    <div class="title-band">
      <span class="title-band__name">MARA QUILL</span>
      <span class="title-band__divider"></span>
      <span class="title-band__role">GENERAL MANAGER</span>
    </div>

    <div class="contacts">
      <div class="contact">
        <svg class="contact__icon" viewBox="0 0 22 22" aria-hidden="true">
          <circle cx="11" cy="11" r="10" fill="none" stroke="var(--ink)" stroke-width="1.5"/>
          <path d="M7.5 6.5l2 0 1 2.5-1.3 1a6 6 0 0 0 2.8 2.8l1-1.3 2.5 1v2a1 1 0 0 1-1 1A8 8 0 0 1 6.5 7.5a1 1 0 0 1 1-1z" fill="var(--ink)"/>
        </svg>
        021 884 7261
      </div>
      <div class="contact">
        <svg class="contact__icon" viewBox="0 0 22 22" aria-hidden="true">
          <circle cx="11" cy="11" r="10" fill="var(--ink)"/>
          <rect x="6" y="7.5" width="10" height="7" rx="1" fill="none" stroke="#fff" stroke-width="1.3"/>
          <path d="M6.5 8l4.5 3.5L15.5 8" fill="none" stroke="#fff" stroke-width="1.3"/>
        </svg>
        tidelark77@mailvesta.test
      </div>
      <div class="contact">
        <svg class="contact__icon" viewBox="0 0 22 22" aria-hidden="true">
          <circle cx="11" cy="11" r="10" fill="none" stroke="var(--ink)" stroke-width="1.5"/>
          <rect x="8" y="5.5" width="6" height="11" rx="1.2" fill="none" stroke="var(--ink)" stroke-width="1.3"/>
          <circle cx="11" cy="14.3" r=".8" fill="var(--ink)"/>
        </svg>
        03 555 0142
      </div>
      <div class="contact">
        <svg class="contact__icon" viewBox="0 0 22 22" aria-hidden="true">
          <circle cx="11" cy="11" r="10" fill="var(--ink)"/>
          <circle cx="11" cy="11" r="5.5" fill="none" stroke="#fff" stroke-width="1.2"/>
          <ellipse cx="11" cy="11" rx="2.3" ry="5.5" fill="none" stroke="#fff" stroke-width="1.2"/>
          <line x1="5.5" y1="11" x2="16.5" y2="11" stroke="#fff" stroke-width="1.2"/>
        </svg>
        www.byteharbour.test
      </div>
      <div class="contact contact--wide">
        <svg class="contact__icon" viewBox="0 0 22 22" aria-hidden="true">
          <circle cx="11" cy="11" r="10" fill="none" stroke="var(--ink)" stroke-width="1.5"/>
          <path d="M11 5a4 4 0 0 1 4 4c0 3-4 7.5-4 7.5S7 12 7 9a4 4 0 0 1 4-4z" fill="var(--ink)"/>
          <circle cx="11" cy="9" r="1.4" fill="#fff"/>
        </svg>
        14c Marlowe Cres, Fenwick
      </div>
    </div>
  </section>

</body>
</html>
```